Brand new redesign of Brightpath finance website

I need a new website design that i can advertise a great low interest rate on the front page and capture input application details that will send through to my email address.

some car finance companies will be similar to this would be listed below

tallowcredit.example.com.au
mirabelfinance.example.com.au
finance725.example.com.au
quenbyfinance.example.com.au
finance91.example.com.au

Reason: I have changed the project to a committed project. all the webpages should have the same format just different content and i want to be able to edit the front page easily to update my interest rates.

Target Market(s)

Australian Finance market targeting a younger demographic

Industry/Entity Type

Finance

Coding

Coded - Design and coding required

Number of Pages Required

5+ page

Font styles to use
Serif
Sans Serif

Colors
0255a3
ffffff
cedeed

Requirements
Must have
• application capture form
• apply now buttons
• Headline rate front page

```html
<!DOCTYPE html>
<html lang="en">
<head>
<meta charset="utf-8">
<title>Brightpath Finance</title>
<link rel="stylesheet" href="https://fonts.googleapis.com/css2?family=Lato:wght@400;700;900&family=Cabin:wght@500;600;700&display=swap">
<style>
:root{
  --navy:#2b3891;
  --navy-deep:#232c7a;
  --brand:#0255a3;
  --sky:#1aa3e0;
  --sky-light:#35b7ec;
  --pale:#cedeed;
  --ink:#222;
  --muted:#555;
  --white:#fff;
  --black:#0d0d0d;
  --footer:#343434;
  --footer-deep:#1e1e1e;
}
*{box-sizing:border-box;margin:0;padding:0}
html,body{width:1200px;height:2503px;overflow:hidden;background:var(--white)}
body{font-family:'Lato',sans-serif;color:var(--ink);position:relative}
.abs{position:absolute}

/* top bar */
.topbar{left:0;top:0;width:1200px;height:37px;background:var(--black)}
.topbar .social{position:absolute;top:11px;width:16px;height:16px;border-radius:50%;background:#e6e6e6}
.apply-now{position:absolute;left:991px;top:0;width:127px;height:37px;background:var(--sky);color:var(--white);font-size:14px;font-weight:700;display:flex;align-items:center;justify-content:center;gap:8px}

/* header */
.brand{left:82px;top:48px;display:flex;align-items:center;gap:12px}
.brand-mark{width:46px;height:46px;border-radius:50%;background:var(--navy)}
.brand-name{font-family:'Cabin',sans-serif;font-weight:700;font-size:26px;color:var(--navy);line-height:1}
.contact-item{display:flex;gap:12px;align-items:center}
.contact-item .label{font-size:15px;font-weight:700;color:#333}
.contact-item .value{font-size:15px;color:#444;margin-top:3px}

/* nav */
.mainnav{left:0;top:163px;width:1200px;height:45px;background:var(--navy);display:flex;padding-left:82px}
.mainnav a{color:var(--white);text-decoration:none;font-size:13.5px;font-weight:700;letter-spacing:.5px;display:flex;align-items:center;justify-content:center;border-right:1px solid rgba(255,255,255,.18)}
.mainnav a.active{background:var(--sky)}

/* hero */
.hero{left:0;top:208px;width:1200px;height:471px;background:linear-gradient(100deg,#c9a98f 0%,#e4cfc0 35%,#d9d6d8 60%,#b9c0c8 100%)}
.hero-title{left:83px;top:465px;font-family:'Cabin',sans-serif;font-weight:700;font-size:36px;color:var(--white);text-shadow:0 2px 4px rgba(0,0,0,.35)}
.tag{position:absolute;height:38px;background:rgba(40,40,40,.78);border-left:4px solid var(--sky);color:var(--white);font-size:15px;font-weight:700;display:flex;align-items:center;padding-left:14px}
.quote{left:806px;top:235px;width:311px;height:406px;background:rgba(25,25,30,.85);border:3px solid #666}
.quote-head{height:46px;display:flex;align-items:center;justify-content:center;color:#7fd3ff;font-family:'Cabin',sans-serif;font-weight:700;font-size:21px;background:rgba(255,255,255,.08)}
.field{position:absolute;left:20px;width:265px;height:34px;background:var(--white);font-size:12.5px;color:#333;display:flex;align-items:center;padding-left:14px}
.terms{position:absolute;left:20px;top:300px;display:flex;align-items:center;gap:10px;color:var(--white);font-size:12.5px}
.terms .box{width:15px;height:15px;background:var(--white)}
.quote-btn{position:absolute;left:20px;top:338px;width:265px;height:45px;background:var(--sky);color:var(--white);font-weight:900;font-size:18px;display:flex;align-items:center;justify-content:center}

/* section titles */
.section-title{position:absolute;left:0;width:1200px;text-align:center;font-family:'Cabin',sans-serif;font-weight:700;font-size:31px;letter-spacing:.5px}
.divider{position:absolute;left:340px;width:520px;height:16px}
.divider::before,.divider::after{content:"";position:absolute;top:7px;width:240px;height:1px;background:#d9d9d9}
.divider::before{left:0}.divider::after{right:0}
.divider span{position:absolute;left:252px;top:0;width:16px;height:16px;border-radius:50%;border:2px solid var(--sky)}
.divider.light::before,.divider.light::after{background:rgba(255,255,255,.45)}
.divider.light span{border-color:var(--white)}

.intro{left:92px;top:818px;width:1018px;text-align:center;font-size:14px;line-height:25px;color:#222}
.call-box{left:350px;top:918px;width:498px;height:42px;border:1px solid #ddd;display:flex;align-items:center;font-size:27px;color:#222}
.call-box .ico{width:46px;height:46px;margin-left:-2px;border-radius:50%;border:2px solid var(--sky);background:var(--white);display:flex;align-items:center;justify-content:center;margin-right:22px}

/* loans */
.loans{left:0;top:1006px;width:1200px;height:376px;background:linear-gradient(120deg,#1da9dd 0%,#36b8ea 45%,#1d94d0 100%)}
.loan-card{position:absolute;top:132px;width:239px;height:157px;border:4px solid var(--white);box-shadow:0 3px 8px rgba(0,0,0,.25)}
.loan-label{position:absolute;top:304px;width:239px;text-align:center;color:var(--white);font-family:'Cabin',sans-serif;font-weight:600;font-size:23px;letter-spacing:.5px}

/* solutions */
.sol-ico{position:absolute;width:74px;height:74px;border-radius:50%;background:var(--sky);display:flex;align-items:center;justify-content:center}
.sol-text{position:absolute;width:280px}
.sol-text h3{font-family:'Cabin',sans-serif;font-weight:700;font-size:19px;color:#222;letter-spacing:.3px;line-height:23px}
.sol-text p{font-size:11.5px;color:#555;line-height:19px;margin-top:6px}
.sol-text.left{text-align:right}
.hub{left:502px;top:1556px;width:198px;height:198px;border-radius:50%;background:var(--navy);box-shadow:0 0 0 8px #e9ecf6;display:flex;flex-direction:column;align-items:center;justify-content:center;color:var(--white);font-family:'Cabin',sans-serif;font-weight:600;font-size:21px;text-align:center;line-height:25px}
.hub .dot{width:56px;height:56px;border-radius:50%;background:rgba(255,255,255,.85);margin-bottom:12px}

/* cta */
.cta{position:absolute;top:1821px;width:600px;height:444px;color:var(--white);text-align:center}
.cta.left{left:0;background:linear-gradient(135deg,#3240a8,#2a3596)}
.cta.right{left:600px;background:linear-gradient(135deg,#1e9ad8,#1686c6)}
.cta h2{position:absolute;left:0;width:100%;top:152px;font-family:'Cabin',sans-serif;font-weight:700;font-size:28px;line-height:39px;letter-spacing:.6px}
.cta p{position:absolute;left:0;width:100%;top:252px;font-size:18px;line-height:29px}
.cta .btn{position:absolute;top:340px;height:46px;display:flex;align-items:center;justify-content:center;font-weight:900;font-size:18px;letter-spacing:.5px}
.cta.left .btn{left:207px;width:265px;background:var(--sky)}
.cta.right .btn{left:128px;width:267px;background:var(--navy)}

/* footer */
.footer{left:0;top:2265px;width:1200px;height:194px;background:var(--footer)}
.footnav{position:absolute;top:46px;left:0;width:1200px;display:flex;justify-content:center;gap:40px;font-size:13.5px;font-weight:700;color:var(--white);letter-spacing:.3px}
.footrule{position:absolute;left:82px;top:88px;width:1036px;height:1px;background:#555}
.finfo{position:absolute;top:110px;display:flex;gap:12px;color:var(--white);font-size:14px;line-height:22px;white-space:nowrap}
.finfo .pin{width:30px;height:30px;border-radius:50%;background:var(--sky);flex:none;display:flex;align-items:center;justify-content:center;margin-top:4px}
.finfo b{font-weight:700}
.fsocial{position:absolute;top:117px;width:32px;height:32px;border-radius:50%}
.copyright{left:0;top:2459px;width:1200px;height:44px;background:var(--footer-deep);color:var(--white);font-size:13px;display:flex;align-items:center;justify-content:center;border-top:2px solid var(--navy)}
</style>
</head>
<body>

<header>
  <div class="abs topbar">
    <span class="social" style="left:852px"></span>
    <span class="social" style="left:885px"></span>
    <span class="social" style="left:924px"></span>
    <span class="social" style="left:962px"></span>
    <div class="apply-now">
      <svg width="18" height="18" viewBox="0 0 18 18"><rect x="1" y="4" width="12" height="12" fill="none" stroke="#fff" stroke-width="1.6"/><path d="M7 11 L16 2" stroke="#fff" stroke-width="2"/></svg>
      Apply Now
    </div>
  </div>

  <div class="abs brand">
    <span class="brand-mark"></span>
    <span class="brand-name">BRIGHTPATH FINANCE</span>
  </div>

  <div class="abs contact-item" style="left:604px;top:72px">
    <svg width="34" height="40" viewBox="0 0 34 40"><circle cx="17" cy="20" r="15" fill="none" stroke="var(--sky)" stroke-width="2"/><path d="M11 11c2-1 4 3 4 4s-2 2-1 4 3 5 5 5 2-2 3-1 4 3 3 5c-5 4-18-10-14-17z" fill="var(--navy)"/></svg>
    <div><div class="label">Worried About Finance?</div><div class="value">1300 555 019</div></div>
  </div>
  <div class="abs contact-item" style="left:881px;top:72px">
    <svg width="38" height="36" viewBox="0 0 38 36"><rect x="3" y="8" width="30" height="22" fill="none" stroke="var(--sky)" stroke-width="2.2"/><path d="M3 8 L18 21 L33 8" fill="none" stroke="var(--navy)" stroke-width="2.2"/></svg>
    <div><div class="label">Mail Us:</div><div class="value">info@brightpath.example.com</div></div>
  </div>

  <nav class="abs mainnav">
    <a class="active" style="width:87px">HOME</a>
    <a style="width:132px">ABOUT US</a>
    <a style="width:132px">VEHICLE LOANS</a>
    <a style="width:126px">OTHER LOANS</a>
    <a style="width:133px">INSURANCE</a>
    <a style="width:177px">FINANCE CALCULATOR</a>
    <a style="width:148px;border-right:0">CONTACT US</a>
  </nav>
</header>

<main>
  <section>
    <div class="abs hero" role="img" aria-label="Photo of a smiling family of four beside a new car, the daughter holding up car keys"></div>
    <h1 class="abs hero-title">GET CAR LOANS</h1>
    <div class="tag" style="left:83px;top:534px;width:503px">LOW RATE CAR LOANS FROM 4.69% COMPARISON RATE 4.99%</div>
    <div class="tag" style="left:83px;top:578px;width:185px">LOW FEES</div>
    <div class="tag" style="left:277px;top:578px;width:309px">LOW TOTAL COST LOANS</div>

    <form class="abs quote">
      <div class="quote-head">QUICK &amp; EASY QUOTE</div>
      <div class="field" style="top:70px">First Name</div>
      <div class="field" style="top:114px">Last Name</div>
      <div class="field" style="top:158px">Email Address</div>
      <div class="field" style="top:202px">Phone Number</div>
      <div class="field" style="top:246px;justify-content:space-between;padding-right:10px">Loan Amount In Dollars
        <svg width="12" height="10" viewBox="0 0 12 10"><path d="M0 0 H12 L6 9z" fill="#111"/></svg></div>
      <div class="terms"><span class="box"></span>I Agree To The Terms &amp; Conditions</div>
      <div class="quote-btn">GET MY BEST RATE NOW</div>
    </form>
  </section>

  <section>
    <h2 class="section-title" style="top:722px;color:var(--navy)">ONLINE LOAN PRE APPROVAL</h2>
    <div class="divider" style="top:772px"><span></span></div>
    <p class="abs intro">Complete Our Short Online Application To Get Finance For Your Car, Truck, Motorbike, Equipment, Boat Or Caravan! We Have Helped Thousands Of Australians Obtain The Finance They Need To Buy A New Or Used Vehicle. We'll Find You Competitive Vehicle Finance That'll Get You On The Road Fast And If You've Had Credit Issues In The Past, We Also Have Access To Specialist Lenders Who Could Help.</p>
    <div class="abs call-box">
      <span class="ico"><svg width="22" height="22" viewBox="0 0 22 22"><path d="M4 2c3-1 5 4 5 5s-3 2-2 4 3 5 5 5 2-3 3-2 5 3 4 5C13 25-4 8 4 2z" fill="#222"/></svg></span>
      Call Us Anytime -1300 555 019
    </div>
  </section>

  <section class="abs loans">
    <h2 class="section-title" style="top:36px;color:var(--white)">LOANS WE PROVIDE</h2>
    <div class="divider light" style="top:86px"><span></span></div>
    <div class="loan-card" role="img" aria-label="Photo of a woman receiving car keys" style="left:80px;background:linear-gradient(135deg,#c7b9a6,#e6dfd6)"></div>
    <div class="loan-card" role="img" aria-label="Photo of a white motor yacht on deep blue water" style="left:347px;background:linear-gradient(180deg,#1f3a6b,#0d2248)"></div>
    <div class="loan-card" role="img" aria-label="Photo of a couple walking toward an outline of a house" style="left:614px;background:linear-gradient(180deg,#a9c4e6,#d7c6a4)"></div>
    <div class="loan-card" role="img" aria-label="Photo of a loan adviser shaking hands with a client across a desk" style="left:880px;background:linear-gradient(135deg,#d9cfc6,#f1ece6)"></div>
    <div class="loan-label" style="left:80px">Vehicle Loan</div>
    <div class="loan-label" style="left:347px">Boat Loan</div>
    <div class="loan-label" style="left:614px">Home Loan</div>
    <div class="loan-label" style="left:880px">Personal Loan</div>
  </section>

  <section>
    <h2 class="section-title" style="top:1422px;color:var(--navy)">OUR SOLUTIONS</h2>
    <div class="divider" style="top:1472px"><span></span></div>

    <svg class="abs" style="left:430px;top:1550px" width="340" height="210" viewBox="0 0 340 210">
      <g fill="none" stroke="var(--navy)" stroke-width="1.6" stroke-dasharray="3 4">
        <path d="M8 17 H60 L90 60"/><path d="M8 172 H45 L85 140"/>
        <path d="M332 17 H280 L250 60"/><path d="M332 172 H295 L255 140"/>
      </g>
    </svg>

    <div class="abs hub"><span class="dot"></span>BRIGHTPATH<br>SOLUTIONS</div>

    <div class="sol-ico" style="left:362px;top:1530px"><svg width="34" height="38" viewBox="0 0 34 38"><circle cx="17" cy="10" r="8" fill="#fff"/><path d="M2 38c0-10 6-16 15-16s15 6 15 16z" fill="#fff"/></svg></div>
    <div class="sol-ico" style="left:362px;top:1671px"><svg width="38" height="32" viewBox="0 0 38 32"><rect x="2" y="4" width="9" height="26" fill="#fff"/><rect x="14" y="2" width="9" height="28" fill="#fff"/><rect x="26" y="6" width="9" height="24" fill="#fff"/></svg></div>
    <div class="sol-ico" style="left:765px;top:1527px"><svg width="38" height="38" viewBox="0 0 38 38"><circle cx="20" cy="12" r="9" fill="#fff"/><path d="M2 26h10l8 3h10l6-4v6l-8 5H2z" fill="#fff"/></svg></div>
    <div class="sol-ico" style="left:765px;top:1671px"><svg width="34" height="38" viewBox="0 0 34 38"><rect x="3" y="2" width="22" height="30" fill="#fff"/><circle cx="24" cy="26" r="7" fill="none" stroke="#fff" stroke-width="3"/><path d="M29 31l4 5" stroke="#fff" stroke-width="3"/></svg></div>

    <div class="sol-text left" style="left:62px;top:1528px"><h3>BAS AGENT</h3><p>Lorem ipsum dolor sit amet, consectetuer<br>adipiscing elit, sed diam nonummy nibh euismod</p></div>
    <div class="sol-text left" style="left:62px;top:1666px"><h3>PAYROLL &amp; BOOK<br>KEEPING SERVICE</h3><p>Lorem ipsum dolor sit amet, consectetuer<br>adipiscing elit, sed diam nonummy nibh euismod</p></div>
    <div class="sol-text" style="left:858px;top:1525px"><h3>DEBT CONSOLIDATION</h3><p>Lorem ipsum dolor sit amet, consectetuer<br>adipiscing elit, sed diam nonummy nibh euismod</p></div>
    <div class="sol-text" style="left:855px;top:1666px"><h3>CREDIT FILE REPAIR /<br>DEFAULT REMOVALS</h3><p>Lorem ipsum dolor sit amet, consectetuer<br>adipiscing elit, sed diam nonummy nibh euismod</p></div>
  </section>

  <section>
    <div class="cta left">
      <svg class="abs" style="left:280px;top:55px" width="52" height="70" viewBox="0 0 52 70"><rect x="3" y="3" width="46" height="64" rx="3" fill="none" stroke="#fff" stroke-width="4"/><rect x="11" y="11" width="30" height="18" fill="#fff"/><g fill="#fff"><rect x="11" y="36" width="8" height="7"/><rect x="22" y="36" width="8" height="7"/><rect x="33" y="36" width="8" height="7"/><rect x="11" y="47" width="8" height="7"/><rect x="22" y="47" width="8" height="7"/><rect x="33" y="47" width="8" height="7"/></g></svg>
      <h2>WHAT WILL MY<br>REPAYMENTS BE?</h2>
      <p>See How Much You Could Borrow With<br>Our Loan Calculator</p>
      <div class="btn">CALCULATE YOUR LOAD</div>
    </div>
    <div class="cta right">
      <svg class="abs" style="left:226px;top:55px" width="70" height="70" viewBox="0 0 70 70"><rect x="2" y="30" width="14" height="36" fill="#fff"/><path d="M20 32 L34 6 c6 0 8 4 6 12 l-3 10 h22 c6 0 8 6 4 10 c3 3 2 8-2 10 c2 4 0 8-4 9 c1 5-2 8-7 8 H20z" fill="#fff"/></svg>
      <h2>WHAT GUARANTEED APPROVAL<br>ACTUALLY MEANS</h2>
      <p>We Explain What It Means And<br>What We Offer Instead</p>
      <div class="btn">CALCULATE YOUR LOAD</div>
    </div>
  </section>
</main>

<footer>
  <div class="abs footer">
    <div class="footnav">
      <span>HOME</span><span>ABOUT US</span><span>VEHICLE LOANS</span><span>OTHER LOANS</span><span>INSURANCE</span><span>FINANCE CALCULATOR</span><span>CONTACT US</span>
    </div>
    <div class="footrule"></div>
    <div class="finfo" style="left:82px">
      <span class="pin"><svg width="12" height="16" viewBox="0 0 12 16"><path d="M6 0a6 6 0 0 1 6 6c0 4-6 10-6 10S0 10 0 6a6 6 0 0 1 6-6z" fill="#fff"/></svg></span>
      <div><b>BRIGHTPATH FINANCE,</b><br>Lorem ipsum dolor sit amet, consectetuer adipi</div>
    </div>
    <div class="finfo" style="left:472px">
      <span class="pin"><svg width="14" height="14" viewBox="0 0 22 22"><path d="M4 2c3-1 5 4 5 5s-3 2-2 4 3 5 5 5 2-3 3-2 5 3 4 5C13 25-4 8 4 2z" fill="#fff"/></svg></span>
      <div><b>Call Us :</b><br>+61 2 5550 1948</div>
    </div>
    <div class="finfo" style="left:678px">
      <span class="pin"><svg width="14" height="12" viewBox="0 0 14 12"><rect x="0" y="0" width="14" height="12" fill="#fff"/><path d="M0 0 L7 6 L14 0" fill="none" stroke="var(--sky)" stroke-width="1.5"/></svg></span>
      <div><b>Email Us :</b><br>hello@brightpath.example.com</div>
    </div>
    <span class="fsocial" style="left:953px;background:#3b5ba6"></span>
    <span class="fsocial" style="left:997px;background:#2aa9e0"></span>
    <span class="fsocial" style="left:1041px;background:#1e7bb8"></span>
    <span class="fsocial" style="left:1085px;background:#dd4b39"></span>
  </div>
  <div class="abs copyright">Copyright © 2016 BRIGHTPATH FINANCE &nbsp;|&nbsp; All Rights Reserved.</div>
</footer>

</body>
</html>
```